Fern Lattice Table & Chair Rentals

We need a business card for a table and chair rental company. We rent tables and chairs for weddings, funerals, business events and parties. We want something that looks clean and elegant while not being too busy. We would like colors in the green and blue hues and avoiding anything orange. We want to make sure the font is large enough to be seen easily.

Target Market(s)

Wedding & Event Rentals

Industry/Entity Type

Events

Contact Information for Business Card

Fern Lattice, sales@fernlatticerentals.com, fernlatticerentals.com, 360-555-0182

Requirements
Must have
• Easy to read font
Should not have
• Orange anywhere in the design

```html
<!DOCTYPE html>
<html lang="en">
<head>
<meta charset="utf-8">
<title>Fern Lattice Table and Chair Rentals – Business Card</title>
<link rel="stylesheet" href="https://fonts.googleapis.com/css2?family=PT+Sans:wght@400;700&display=swap">
<style>
  :root {
    --backdrop: #eef2f1;
    --card-fern: #2f7a68;
    --card-white: #ffffff;
    --ink: #1f2a2e;
    --rule-blue: #2a5a86;
    --type-light: #ffffff;
  }
  * { margin: 0; padding: 0; box-sizing: border-box; }
  html, body {
    width: 1200px;
    height: 1189px;
    overflow: hidden;
  }
  body {
    position: relative;
    background: var(--backdrop);
    font-family: "PT Sans", Tahoma, sans-serif;
    color: var(--ink);
  }

  .card {
    position: absolute;
    box-shadow: 0 4px 14px rgba(0, 0, 0, 0.18);
    overflow: hidden;
  }

  /* Front of card */
  .card-front {
    left: 50px;
    top: 80px;
    width: 680px;
    height: 390px;
    background: var(--card-fern);
    color: var(--type-light);
  }
  .card-front .brand-name {
    position: absolute;
    left: 80px;
    top: 110px;
    font-size: 92px;
    font-weight: 400;
    line-height: 1;
  }
  .card-front .tagline {
    position: absolute;
    left: 84px;
    top: 232px;
    font-size: 46px;
    font-weight: 400;
    line-height: 1;
  }

  /* Back of card */
  .card-back {
    left: 760px;
    top: 410px;
    width: 400px;
    height: 720px;
    background: var(--card-white);
  }
  .card-back .brand-block {
    position: absolute;
    right: 30px;
    top: 110px;
  }
  .card-back .brand-name {
    font-size: 50px;
    font-weight: 400;
    line-height: 1;
    margin-left: 22px;
  }
  .card-back .tagline {
    font-size: 25px;
    font-weight: 400;
    line-height: 1.2;
    margin-top: 6px;
  }
  .contact {
    position: absolute;
    left: 0;
    right: 0;
    top: 310px;
    text-align: center;
  }
  .contact .contact-name {
    font-size: 44px;
    font-weight: 700;
    line-height: 1;
    margin-bottom: 50px;
  }
  .contact .phone {
    font-size: 34px;
    font-weight: 700;
    line-height: 1.1;
  }
  .contact .email,
  .contact .city {
    font-size: 22px;
    font-weight: 400;
    line-height: 1.3;
  }
  .card-back .footer-band {
    position: absolute;
    left: 0;
    right: 0;
    bottom: 0;
    height: 82px;
    background: var(--card-fern);
    border-top: 5px solid var(--rule-blue);
    color: var(--type-light);
    font-size: 27px;
    display: flex;
    align-items: center;
    justify-content: center;
  }
</style>
</head>
<body>
  <section class="card card-front" aria-label="Business card front">
    <div class="brand-name">Fern Lattice</div>
    <div class="tagline">Table and Chair Rentals</div>
  </section>

  <section class="card card-back" aria-label="Business card back">
    <div class="brand-block">
      <div class="brand-name">Fern Lattice</div>
      <div class="tagline">Table and Chair Rentals</div>
    </div>
    <div class="contact">
      <div class="contact-name">Fern Lattice</div>
      <div class="phone">360-555-0182</div>
      <div class="email">sales@fernlatticerentals.com</div>
      <div class="city">Alder Bay, Washington</div>
    </div>
    <div class="footer-band">www.fernlatticerentals.com</div>
  </section>
</body>
</html>
```